UI/ UX Design for ERP Software

We need a new UX/UI interface for a ERP software for property managers. Our CMMS / ERP solution is made based on responsive design technologies and is coded in PHP.
The overall UX to be similar to Tev Ulna - easy navigation, intuitive menus.

Industry/Entity Type

Property Management

Number of Pages Required

5+ page

Requirements
Must have
• Round dock buttons
Consistent icons across the application
Enough Spacing between buttons/icons/ menu
Consistent Font
Nice to have
• We would like the UX to allow the users to use the application without /minimum training.
Should not have
• we don't want anything that is classic with respect to UX

```html
<!DOCTYPE html>
<html lang="en">
<head>
<meta charset="utf-8">
<title>Domivo Dashboard</title>
<link href="https://fonts.googleapis.com/css2?family=Poppins:wght@400;500;600&display=swap" rel="stylesheet">
<style>
:root{
  --blue:#0a84ff;
  --ink:#2f3a4a;
  --slate:#4d5b6e;
  --bg:#efefef;
  --white:#ffffff;
  --row:#f3f5f8;
  --line:#e3e6ea;
  --menu:#5aa9ea;
}
*{margin:0;padding:0;box-sizing:border-box}
html,body{width:1200px;height:949px;overflow:hidden}
body{background:var(--bg);font-family:"Poppins",sans-serif;color:var(--ink);position:relative}
.topbar{position:absolute;left:0;top:0;width:1200px;height:90px;background:var(--white);box-shadow:0 1px 4px rgba(0,0,0,.05)}
.brand{position:absolute;left:100px;top:24px;display:flex;align-items:center;gap:10px;font-size:32px;font-weight:600;color:var(--blue);line-height:1}
.brand-mark{width:28px;height:28px;background:var(--blue);border-radius:4px}
.search{position:absolute;left:333px;top:23px;width:468px;height:47px;border:1px solid #b9bec5;border-radius:24px;display:flex;align-items:center;padding:0 20px;font-size:17px;color:#5b6470;justify-content:space-between}
.user{position:absolute;left:961px;top:41px;font-size:13px;font-weight:500;color:var(--ink);display:flex;align-items:center;gap:6px}
.avatar{position:absolute;left:1043px;top:25px;width:50px;height:50px;border-radius:50%;background:linear-gradient(135deg,#c9b3a0,#6f625a)}
.menu{position:absolute;left:1112px;top:36px;width:36px}
.menu span{display:block;height:5px;background:var(--menu);border-radius:3px;margin-bottom:7px}
.card{position:absolute;top:159px;height:200px;background:var(--white)}
.card svg{position:absolute;top:29px}
.card .label{position:absolute;top:123px;font-size:19px;font-weight:500;color:var(--slate)}
.card .value{position:absolute;top:150px;font-size:25px;font-weight:500;color:var(--blue)}
.grid{position:absolute;left:86px;top:388px;width:1028px;background:var(--white);border:1px solid var(--line)}
.row{display:grid;grid-template-columns:95px 192px 201px 161px 192px 187px}
.row > div{display:flex;align-items:center}
.head{background:var(--blue);height:62px}
.head > div{color:var(--white);font-size:15px;border-right:1px solid rgba(255,255,255,.7)}
.head > div:last-child{border-right:none}
.body{background:var(--row);height:50px;margin-top:4px}
.body:first-of-type{margin-top:0}
.body > div{font-size:12px;color:var(--ink);border-right:1px solid var(--line)}
.body > div:last-child{border-right:none;font-size:13px}
.c1{padding-left:23px}.c2{padding-left:39px}.c3{padding-left:51px}.c4{padding-left:45px}.c5{padding-left:40px}.c6{padding-left:50px}
.head .c3{padding-left:53px}.head .c6{padding-left:60px}
.body .c5{padding-left:40px}
</style>
</head>
<body>
<header class="topbar">
  <div class="brand"><span class="brand-mark"></span>Domivo</div>
  <div class="search">Search
    <svg width="18" height="18" viewBox="0 0 24 24"><circle cx="10" cy="10" r="7" fill="none" stroke="#2f3a4a" stroke-width="3"/><line x1="15" y1="15" x2="21" y2="21" stroke="#2f3a4a" stroke-width="3" stroke-linecap="round"/></svg>
  </div>
  <div class="user">Arlo Venn <svg width="9" height="6" viewBox="0 0 9 6"><path d="M1 1l3.5 3.5L8 1" fill="none" stroke="#2f3a4a" stroke-width="1.3"/></svg></div>
  <div class="avatar" role="img" aria-label="User profile photo"></div>
  <div class="menu"><span></span><span></span><span></span></div>
</header>

<section class="card" style="left:86px;width:324px">
  <svg style="left:64px" width="56" height="56" viewBox="0 0 56 56"><path d="M28 4L2 27l4 4 4-3.5V50h13V36h10v14h13V27.5l4 3.5 4-4L44 13V6h-6v2z" fill="var(--blue)"/></svg>
  <div class="label" style="left:66px">PROPERTIES</div>
  <div class="value" style="left:64px">00003</div>
</section>

<section class="card" style="left:425px;width:324px">
  <svg style="left:65px" width="56" height="56" viewBox="0 0 56 56"><circle cx="23" cy="17" r="12" fill="var(--blue)"/><circle cx="23" cy="19" r="7" fill="#fff"/><path d="M2 56c0-14 8-21 21-21 6 0 10 1 13 4L25 48v8z" fill="var(--blue)"/><path d="M44 36l12 10v10H32V46z" fill="var(--blue)"/><rect x="41" y="48" width="6" height="8" fill="#fff"/></svg>
  <div class="label" style="left:66px">TENANTS</div>
  <div class="value" style="left:65px">00008</div>
</section>

<section class="card" style="left:761px;width:353px">
  <svg style="left:55px" width="56" height="56" viewBox="0 0 56 56"><path d="M0 0h28v7H7v42h42V28h7v28H0z" fill="var(--blue)"/><path d="M34 0h22v22h-7V12L27 34l-5-5L44 7H34z" fill="var(--blue)"/></svg>
  <div class="label" style="left:56px">TOTAL PROPETIES AREA</div>
  <div class="value" style="left:55px">422,000.00 sq.ft</div>
</section>

<section class="grid">
  <div class="row head"><div class="c1">ID</div><div class="c2">DATE &amp; TIME</div><div class="c3">REQUEST TYPE</div><div class="c4">CURRENCY</div><div class="c5">PROPERTIES</div><div class="c6">STATUS</div></div>
  <div class="row body"><div class="c1">4527</div><div class="c2">15/01/2021&nbsp;&nbsp; 2 Hr</div><div class="c3">Loremis</div><div class="c4">USD</div><div class="c5">$25, 485,25</div><div class="c6">Dummy lorem</div></div>
  <div class="row body"><div class="c1">4527</div><div class="c2">15/01/2021&nbsp;&nbsp; 2 Hr</div><div class="c3">Loremis</div><div class="c4">USD</div><div class="c5">$25, 485,25</div><div class="c6">Dummy lorem</div></div>
  <div class="row body"><div class="c1">4527</div><div class="c2">15/01/2021&nbsp;&nbsp; 2 Hr</div><div class="c3">Loremis</div><div class="c4">USD</div><div class="c5">$25, 485,25</div><div class="c6">Dummy lorem</div></div>
  <div class="row body"><div class="c1">4527</div><div class="c2">15/01/2021&nbsp;&nbsp; 2 Hr</div><div class="c3">Loremis</div><div class="c4">USD</div><div class="c5">$25, 485,25</div><div class="c6">Dummy lorem</div></div>
  <div class="row body"><div class="c1">4527</div><div class="c2">15/01/2021&nbsp;&nbsp; 2 Hr</div><div class="c3">Loremis</div><div class="c4">USD</div><div class="c5">$25, 485,25</div><div class="c6">Dummy lorem</div></div>
  <div class="row body"><div class="c1">4527</div><div class="c2">15/01/2021&nbsp;&nbsp; 2 Hr</div><div class="c3">Loremis</div><div class="c4">USD</div><div class="c5">$25, 485,25</div><div class="c6">Dummy lorem</div></div>
  <div class="row body"><div class="c1">4527</div><div class="c2">15/01/2021&nbsp;&nbsp; 2 Hr</div><div class="c3">Loremis</div><div class="c4">USD</div><div class="c5">$25, 485,25</div><div class="c6">Dummy lorem</div></div>
  <div class="row body"><div class="c1">4527</div><div class="c2">15/01/2021&nbsp;&nbsp; 2 Hr</div><div class="c3">Loremis</div><div class="c4">USD</div><div class="c5">$25, 485,25</div><div class="c6">Dummy lorem</div></div>
</section>
</body>
</html>
```